Veltrane Group Business Card Design

The CEO is looking for a new trendy look for his business card.
You can stay with current branding or come up with something new/creative. It can be 3D, including Medical Office buildings. You can use our logo in a variety of colors. Please include name, title, company name, company website, email address, cell number

Target Market(s)

Real Estate Development and Construction

Industry/Entity Type

Health care real estate

Contact Information for Business Card

Rohesh Kamdar, CEO M-604.781.2249 E-roheshkamdar@veltrane.com Address:4180 Lindqvist Ave, Tampa, FL 33482 www.veltrane.com

Font styles to use
Other font styles liked:
• Be creative

Requirements
Must have
• Creative, trendy look
Nice to have
• Please go to our website to get a feel- www. veltrane.com
Should not have
• small fonts

```html
<!DOCTYPE html>
<html lang="en">
<head>
<meta charset="utf-8">
<title>Veltrane Group – Business Card</title>
<link rel="stylesheet" href="https://fonts.googleapis.com/css2?family=Roboto:wght@400;700;900&display=swap">
<style>
  :root {
    --stage: #3a3a3a;
    --brand-red: #b0202b;
    --brand-navy: #1e2d4f;
    --ink: #3d3d3d;
    --paper: #ffffff;
    --rule: #c9c9c9;
    --card-w: 520px;
    --card-h: 297px;
  }
  * { margin: 0; padding: 0; box-sizing: border-box; }
  html, body { width: 1200px; height: 689px; overflow: hidden; }
  body {
    background: var(--stage);
    font-family: "Roboto", Arial, sans-serif;
    position: relative;
  }
  .card {
    position: absolute;
    width: var(--card-w);
    height: var(--card-h);
    border-radius: 18px;
    overflow: hidden;
  }
  /* Back side */
  .card-back {
    left: 50px;
    top: 95px;
    background: var(--brand-red);
  }
  .card-back .wordmark {
    position: absolute;
    left: 0; right: 0;
    top: 104px;
    text-align: center;
    font-weight: 900;
    font-size: 54px;
    letter-spacing: -1px;
    color: #d0394a;
  }
  .card-back .website {
    position: absolute;
    left: 0; right: 0;
    bottom: 52px;
    text-align: center;
    color: var(--paper);
    font-size: 14px;
    letter-spacing: 3px;
  }
  /* Front side */
  .card-front {
    left: 630px;
    top: 297px;
    background: var(--paper);
  }
  .swoosh { position: absolute; left: 0; top: 0; width: 100%; height: 100%; z-index: 0; }
  .swoosh .band-navy { fill: var(--brand-navy); }
  .swoosh .band-red { fill: var(--brand-red); }
  .card-front .wordmark {
    position: absolute;
    z-index: 1;
    left: 26px;
    top: 104px;
    width: 210px;
    font-weight: 900;
    font-size: 34px;
    line-height: 1.02;
    letter-spacing: -1px;
    color: var(--brand-red);
  }
  .card-front .divider {
    position: absolute;
    z-index: 1;
    left: 250px;
    top: 34px;
    width: 1px;
    height: 140px;
    background: var(--rule);
  }
  .contact {
    position: absolute;
    z-index: 1;
    left: 268px;
    top: 28px;
    color: var(--ink);
  }
  .contact .person-name {
    font-weight: 700;
    font-size: 21px;
    color: var(--brand-red);
  }
  .contact .person-title {
    font-size: 13px;
    color: var(--brand-navy);
    margin-bottom: 10px;
  }
  .contact .address {
    font-size: 13px;
    line-height: 1.3;
    margin-bottom: 8px;
  }
  .contact .line {
    display: flex;
    align-items: center;
    gap: 7px;
    font-size: 13px;
    line-height: 1.4;
  }
  .contact .line svg { width: 11px; height: 11px; fill: var(--brand-red); flex: none; }
</style>
</head>
<body>
  <section class="card card-back" aria-label="Card back">
    <div class="wordmark">Veltrane Group</div>
    <div class="website">www.veltrane.com</div>
  </section>

  <section class="card card-front" aria-label="Card front">
    <svg class="swoosh" viewBox="0 0 520 297" preserveAspectRatio="none" aria-hidden="true">
      <path class="band-navy" d="M0 272 C200 262 400 230 520 196 L520 208 C400 242 200 272 0 280 Z"/>
      <path class="band-red" d="M0 280 C200 272 400 242 520 208 L520 297 L0 297 Z"/>
    </svg>
    <div class="wordmark">Veltrane Group</div>
    <div class="divider"></div>
    <div class="contact">
      <div class="person-name">Rohesh Kamdar</div>
      <div class="person-title">CEO</div>
      <div class="address">4180 Lindqvist Ave, Tampa,<br>FL 33482</div>
      <div class="line">
        <svg viewBox="0 0 16 16" aria-hidden="true"><path d="M3.6 1.2l2.2 2.9-1.3 1.6c.9 2 2.6 3.7 4.6 4.6l1.6-1.3 2.9 2.2-1.1 2.5C6.6 13.6 2.4 9.4 1.1 2.3z"/></svg>
        <span>604.781.2249</span>
      </div>
      <div class="line">
        <svg viewBox="0 0 16 16" aria-hidden="true"><path d="M1 3h14v10H1z M1 3l7 6 7-6" stroke="#fff" stroke-width="1.2"/></svg>
        <span>roheshkamdar@veltrane.com</span>
      </div>
      <div class="line">
        <svg viewBox="0 0 16 16" aria-hidden="true"><circle cx="8" cy="8" r="7"/></svg>
        <span>www.veltrane.com</span>
      </div>
    </div>
  </section>
</body>
</html>
```